q-zen design for startup inpection service

building and pest inspections what i had in mind was q-zen in large print with prepurchase in small print directly under it and the small tm (tradmark) .Within the C I would like an eye but I don't want to take away from the C so maybe the eye would be done in a fine line?I would also like the Building and Pest inspections to be prominent and large .Have no idea of colors but do like black orange and silver

Target Market(s)

home buyers and realestate agents

Industry/Entity Type

Building

Contact Information for Business Card

q-zen prepurchase, Phone 0412093816, fax 02 71934058, email q-zen@mailbrook.com.au ,building and pest inspections

Font styles to use
Sans Serif

Requirements
Must have
• bold color
• simple layout
• bold color
• uncluttered layout
Should not have
• contact details the same size as Building and Pest Inspections

```html
<!DOCTYPE html>
<html lang="en">
<head>
<meta charset="utf-8">
<title>Q-Zen Building and Pest Inspections – Business Card</title>
<link href="https://fonts.googleapis.com/css2?family=Open+Sans:wght@400;700&display=swap" rel="stylesheet">
<style>
  :root {
    --backdrop: #2a2d31;
    --navy: #0b1f2e;
    --sky: #41b1d9;
    --coral: #f06553;
    --white: #ffffff;
    --ink: #11283b;
    --brand: #1f3f7f;
  }
  html, body {
    margin: 0;
    width: 1200px;
    height: 970px;
    overflow: hidden;
    background: var(--backdrop);
    font-family: "Open Sans", sans-serif;
  }
  .card {
    position: absolute;
    left: 140px;
    top: 222px;
    width: 922px;
    height: 526px;
    background: var(--navy);
    overflow: hidden;
  }
  .card__bands {
    position: absolute;
    inset: 0;
  }
  .card__name,
  .card__service {
    position: absolute;
    left: 0;
    width: 100%;
    margin: 0;
    text-align: center;
    color: var(--white);
    font-weight: 700;
    text-shadow: 0 3px 6px rgba(0, 0, 0, 0.55);
  }
  .card__name {
    top: 88px;
    font-size: 66px;
    line-height: 1;
    padding-left: 40px;
    box-sizing: border-box;
  }
  .card__service {
    top: 170px;
    font-size: 50px;
    line-height: 1;
    padding-left: 80px;
    box-sizing: border-box;
  }
  .contact {
    position: absolute;
    left: 36px;
    margin: 0;
    font-size: 26px;
    line-height: 1;
    letter-spacing: 0.3px;
  }
  .contact--phone { top: 311px; color: var(--ink); }
  .contact--fax   { top: 384px; left: 40px; color: var(--white); }
  .contact--email { top: 447px; left: 38px; color: var(--ink); }
  .brand {
    position: absolute;
    left: 590px;
    top: 330px;
    display: flex;
    align-items: center;
    gap: 16px;
  }
  .brand__dot {
    width: 58px;
    height: 58px;
    border-radius: 50%;
    background: var(--brand);
  }
  .brand__name {
    color: var(--brand);
    font-size: 64px;
    font-weight: 700;
    line-height: 1;
  }
</style>
</head>
<body>
  <section class="card" aria-label="Q-Zen business card">
    <svg class="card__bands" width="922" height="526" viewBox="0 0 922 526" aria-hidden="true">
      <rect x="0" y="290" width="922" height="206" fill="var(--white)"/>
      <polygon points="0,298 472,298 505,352 0,352" fill="var(--sky)"/>
      <polygon points="0,366 510,366 543,419 0,419" fill="var(--navy)"/>
      <polygon points="0,433 548,433 582,488 0,488" fill="var(--coral)"/>
      <rect x="890" y="298" width="32" height="54" fill="var(--sky)"/>
      <rect x="890" y="366" width="32" height="53" fill="var(--navy)"/>
      <rect x="890" y="433" width="32" height="55" fill="var(--coral)"/>
      <!-- phone icon -->
      <path d="M405 316 q6 0 6 9 q0 9 -6 9" fill="none" stroke="var(--white)" stroke-width="3" stroke-linecap="round"/>
      <!-- fax icon -->
      <g fill="none" stroke="var(--white)" stroke-width="1.8">
        <rect x="401" y="382" width="12" height="8"/>
        <rect x="398" y="389" width="18" height="12" rx="1"/>
        <line x1="402" y1="395" x2="412" y2="395"/>
      </g>
      <!-- envelope icon -->
      <g fill="none" stroke="var(--white)" stroke-width="1.8">
        <rect x="400" y="449" width="17" height="12"/>
        <polyline points="400,449 408.5,456 417,449"/>
      </g>
    </svg>

    <h1 class="card__name">Q-Zen</h1>
    <p class="card__service">Building and Pest inspections</p>

    <p class="contact contact--phone">0412093816</p>
    <p class="contact contact--fax">02 71934058</p>
    <p class="contact contact--email">q-zen@mailbrook.com.au</p>

    <div class="brand">
      <span class="brand__dot" aria-hidden="true"></span>
      <span class="brand__name">Q-Zen</span>
    </div>
  </section>
</body>
</html>
```